Marwick Law Letterhead

We need a new letterhead design for a Law Firm. The address for the law firm is 1475 Calloway Street, Suite 210, Houston, Texas 77041. Phone Number: 832-361-9027; Fax Number: 832-614-7359. The logo is uploaded to the project.

```html
<!DOCTYPE html>
<html lang="en">
<head>
<meta charset="utf-8">
<title>Marwick Law Letterhead</title>
<link href="https://fonts.googleapis.com/css2?family=Montserrat:wght@400;500&display=swap" rel="stylesheet">
<style>
  :root {
    --navy: #213769;
    --red: #c8192a;
    --red-deep: #720713;
    --ink: #2b2b2b;
    --paper: #ffffff;
    --backdrop: #e8e8e8;
  }
  * { margin: 0; padding: 0; box-sizing: border-box; }
  html, body { width: 1154px; height: 1200px; overflow: hidden; background: var(--backdrop); }
  body { font-family: "Montserrat", sans-serif; color: var(--ink); }
  .letterhead {
    position: absolute; left: 162px; top: 20px;
    width: 830px; height: 1160px;
    background: var(--paper);
    box-shadow: 0 6px 18px rgba(0,0,0,0.18);
    overflow: hidden;
  }
  .header-band {
    position: absolute; left: 0; top: 0; width: 830px; height: 78px;
    background: linear-gradient(100deg, var(--red-deep) 0%, var(--navy) 38%, var(--navy) 100%);
  }
  .contact { position: absolute; left: 632px; top: 94px; font-size: 13.5px; line-height: 18px; color: #1d1d1d; font-style: normal; }
  .contact-address { margin-bottom: 6px; }
  .contact-line { display: flex; align-items: center; gap: 11px; height: 21px; }
  .contact-line svg { width: 11px; height: 11px; flex: none; }
  .brand { position: absolute; left: 33px; top: 244px; display: flex; align-items: center; gap: 12px; }
  .brand-dot { width: 22px; height: 22px; border-radius: 50%; background: var(--navy); }
  .brand-name { font-size: 32px; font-weight: 500; color: var(--navy); letter-spacing: 0.5px; }
  .recipient { position: absolute; left: 31px; top: 351px; font-size: 13.5px; line-height: 20.6px; }
  .body-copy { position: absolute; left: 33px; top: 436px; width: 768px; font-size: 13.5px; line-height: 20.6px; }
  .body-copy p { text-align: justify; margin-bottom: 20.6px; }
  .closing { position: absolute; left: 31px; top: 928px; font-size: 16px; }
  .signature { position: absolute; left: 31px; top: 960px; width: 94px; height: 32px;
    background: linear-gradient(90deg, #d9d9d9, #efefef); border-radius: 3px; }
</style>
</head>
<body>
<main class="letterhead">
  <div class="header-band" role="img" aria-label="Decorative navy and red header artwork"></div>

  <address class="contact">
    <div class="contact-address">1475 Calloway Street,<br>Suite 210, Houston,<br>Texas 77041</div>
    <div class="contact-line">
      <svg viewBox="0 0 12 12"><path fill="var(--red)" d="M2.5 1 L4.5 1 L5.3 3.5 L4 4.5 C4.6 6 6 7.4 7.5 8 L8.5 6.7 L11 7.5 L11 9.5 C11 10.3 10.3 11 9.5 11 C5 11 1 7 1 2.5 C1 1.7 1.7 1 2.5 1 Z"/></svg>
      <span>832-361-9027</span>
    </div>
    <div class="contact-line">
      <svg viewBox="0 0 12 12"><rect x="3" y="1" width="6" height="3" fill="var(--red)"/><rect x="1" y="4.5" width="10" height="4.5" rx="1" fill="var(--red)"/><rect x="3" y="8" width="6" height="3" fill="var(--red-deep)"/></svg>
      <span>832-614-7359</span>
    </div>
  </address>

  <div class="brand">
    <span class="brand-dot"></span>
    <span class="brand-name">Marwick Law</span>
  </div>

  <div class="recipient">
    Mr/s<br>First Name and Last Name<br>Company Name<br>Address
  </div>

  <section class="body-copy">
    <p>Lorem ipsum dolor sit amet,consectetur adipiscing sed do eiusmod tempor incididunt laboreet dolore magna aliqua.Ut enim ad minim.veniam, quis nostrud exercitation ullamco laboris nisi ut aliquip exea commodo consequat.Lorem ipsum dolor sit amet,consectetur adipiscing sed do eiusmod tempor incididunt.labore et dolore magna aliqua. Ut enim</p>
    <p>Lorem ipsum dolor sit amet, consectetur adipiscing sed do eiusmod tempor incididunt labore et dolore magna aliqua. Ut enim ad minim veniam, quis nostrud exercitation ullamco laboris nisi ut aliquip exea commodo consequat.Duis aute irure dolor in reprehenderit in voluptate velit esse cillum irure dolor in reprehenderit in voluptate velit esse irure</p>
    <p>Lorem ipsum dolor sit amet, consectetur adipiscing sed do eiusmod tempor incididunt labore et dolore magna aliqua. consequat. Duis aute irure dolor in.reprehenderit in voluptate velit esse cillum dolore eu fugiat nulla pariatur. Excepteur sint occaecat cupidatat non proident, sunt in culpa qui officia deserunt mollit,</p>
    <p>Lorem ipsum dolor sit amet, consectetur adipiscing sed do eiusmod tempor incididunt labore et dolore magna aliqua. Ut enim Lorem ipsum dolor sit amet, consectetur adipiscing sed do eiusmod tempor incididunt labore et dolore magna aliqua. Ut enim Lorem ipsum aliqua.ipsum</p>
    <p>Lorem ipsum dolor sit amet, consectetur adipiscing sed do eiusmod tempor incididunt labore et dolore magna aliqua. Ut enim ad minim veniam, quis nostrud exercitation ullamco laboris nisi ut aliquip exea commodo consequat.Duis aute irure dolor in reprehenderit in voluptate velit esse cillum irure dolor in reprehenderit in voluptate velit esse irure</p>
  </section>

  <div class="closing">Regards</div>
  <div class="signature" role="img" aria-label="Handwritten signature of the sender"></div>
</main>
</body>
</html>
```